VOMRA Pty Ltd Business Card

Looking for a simple yet eye-catching double-sided business card design using my company logo on one side and contact details on the other.

Target Market(s)

Government

Industry/Entity Type

Communication Systems Engineering

Contact Information for Business Card

VOMRA Pty Ltd

Requirements
Nice to have
• Would be great to have a QR code so details can be scanned into contacts

```html
<!DOCTYPE html>
<html lang="en">
<head>
<meta charset="utf-8">
<title>VOMRA Pty Ltd Business Card</title>
<link href="https://fonts.googleapis.com/css2?family=Montserrat:wght@400;700&display=swap" rel="stylesheet">
<style>
  :root {
    --backdrop: #dcdcda;
    --card: #ffffff;
    --ink: #37424a;
    --ink-soft: #3f4a52;
    --card-shadow: rgba(40, 44, 48, 0.18);
  }
  * { box-sizing: border-box; margin: 0; padding: 0; }
  html, body {
    width: 1200px;
    height: 801px;
    overflow: hidden;
    background: var(--backdrop);
    font-family: "Montserrat", sans-serif;
    color: var(--ink);
  }
  .sheet {
    width: 1200px;
    height: 801px;
    display: flex;
    align-items: center;
    justify-content: center;
    gap: 48px;
  }
  .card {
    width: 540px;
    height: 310px;
    background: var(--card);
    border-radius: 18px;
    box-shadow: 0 10px 28px var(--card-shadow);
    position: relative;
    overflow: hidden;
  }
  .card--contact {
    display: flex;
    align-items: center;
  }
  .brand {
    display: flex;
    align-items: center;
    gap: 14px;
  }
  .brand__dot {
    border-radius: 50%;
    background: var(--ink);
    flex: none;
  }
  .brand__name {
    font-weight: 700;
    color: var(--ink);
    letter-spacing: 0.04em;
    line-height: 1;
  }
  .card--contact .brand {
    width: 250px;
    justify-content: center;
  }
  .card--contact .brand__dot { width: 30px; height: 30px; }
  .card--contact .brand__name { font-size: 40px; }
  .divider {
    width: 1px;
    height: 200px;
    background: var(--ink);
  }
  .details {
    padding-left: 26px;
    display: flex;
    flex-direction: column;
  }
  .details__name {
    font-weight: 700;
    font-size: 20px;
    letter-spacing: 0.02em;
    text-transform: uppercase;
  }
  .details__role {
    font-size: 13px;
    margin-top: 2px;
    color: var(--ink-soft);
  }
  .details__list {
    list-style: none;
    margin-top: 18px;
    display: flex;
    flex-direction: column;
    gap: 4px;
  }
  .details__item {
    display: flex;
    align-items: center;
    gap: 8px;
    font-size: 13px;
  }
  .details__icon { width: 12px; height: 12px; flex: none; }
  .details__address {
    margin-top: 16px;
    font-size: 13px;
    line-height: 1.4;
    font-style: normal;
  }
  .card--logo {
    display: flex;
    align-items: center;
    justify-content: center;
  }
  .card--logo .brand { gap: 22px; }
  .card--logo .brand__dot { width: 54px; height: 54px; }
  .card--logo .brand__name { font-size: 72px; }
</style>
</head>
<body>
<main class="sheet">
  <section class="card card--contact" aria-label="Business card, contact side">
    <div class="brand">
      <span class="brand__dot"></span>
      <span class="brand__name">VOMRA</span>
    </div>
    <div class="divider"></div>
    <div class="details">
      <h1 class="details__name">Oliver Hastings</h1>
      <p class="details__role">Managing Director</p>
      <ul class="details__list">
        <li class="details__item">
          <svg class="details__icon" viewBox="0 0 12 12" aria-hidden="true"><path fill="var(--ink)" d="M2.3 0.8l2 0 0.6 2.6-1.3 0.9c0.6 1.4 1.7 2.5 3.1 3.1l0.9-1.3 2.6 0.6 0 2c0 0.6-0.5 1.1-1.1 1.1C4.3 9.8 1.2 6.7 1.2 1.9c0-0.6 0.5-1.1 1.1-1.1z"/></svg>
          482 615 903
        </li>
        <li class="details__item">
          <svg class="details__icon" viewBox="0 0 12 12" aria-hidden="true"><rect x="0.5" y="2.5" width="11" height="7.5" rx="1" fill="var(--ink)"/><path d="M1 3l5 3.8L11 3" fill="none" stroke="#fff" stroke-width="1"/></svg>
          admin@vomra.com.au
        </li>
        <li class="details__item">
          <svg class="details__icon" viewBox="0 0 12 12" aria-hidden="true"><circle cx="6" cy="6" r="5.2" fill="var(--ink)"/><path d="M0.8 6h10.4M6 0.8c-2 2.8-2 7.6 0 10.4M6 0.8c2 2.8 2 7.6 0 10.4" fill="none" stroke="#fff" stroke-width="0.8"/></svg>
          www.vomra.com.au
        </li>
      </ul>
      <address class="details__address">24-26 Harlow Street Redfern<br>NSW 2016 Australia</address>
    </div>
  </section>

  <section class="card card--logo" aria-label="Business card, logo side">
    <div class="brand">
      <span class="brand__dot"></span>
      <span class="brand__name">VOMRA</span>
    </div>
  </section>
</main>
</body>
</html>
```